Community Service Organisation information session flyer

I require a flyer to promote an event. The event is an information session about upcoming community service jobs, where interested people can come along to hear about a new service that is opening in the local area in February 2020.

Target Market(s)

People who currently work in the community service sector (family violence, child wellbeing and aboriginal services)

Industry/Entity Type

Non Profit

Colors

Designer to choose colors to be used in the design.

Requirements
Must have
• The document entitled 'The Willow Gate Community Service Announcement' is the content of the flyer. The 3 most prominent logos need to be 'Pellman Lane', 'DRUK' and 'Tenby and District Aboriginal Co-Operative' as per the attached. The 'Willow Gate' logo should be 50% smaller, and on the bottom right hand corner.
Nice to have
• Please refer to this website for an idea of the look and feel:
• https://willowgate.example.org/

```html
<!DOCTYPE html>
<html lang="en">
<head>
<meta charset="utf-8">
<title>The Willow Gate Community Service Announcement</title>
<link rel="stylesheet" href="https://fonts.googleapis.com/css2?family=Outfit:wght@300;400;500;600;700&display=swap">
<style>
  :root {
    --orange: #f07c1b;
    --orange-deep: #e9661a;
    --orange-light: #f9a24a;
    --gold: #fbb15a;
    --slate: #58585e;
    --ink: #2e2e30;
    --text: #3a3a3c;
    --rule: #8a8a8e;
    --paper: #ffffff;
    --backdrop: #ecebe8;
  }
  * { box-sizing: border-box; margin: 0; padding: 0; }
  html, body { width: 1200px; height: 1000px; overflow: hidden; }
  body {
    background: var(--backdrop);
    font-family: "Outfit", "Helvetica Neue", Arial, sans-serif;
    color: var(--text);
    position: relative;
  }
  .flyer {
    position: absolute; left: 260px; top: 19px;
    width: 680px; height: 962px;
    background: var(--paper);
    box-shadow: 0 4px 18px rgba(0,0,0,.12);
    overflow: hidden;
  }
  .hero {
    position: absolute; left: 17px; top: 17px; width: 645px; height: 267px;
    border-radius: 10px 10px 0 0; overflow: hidden;
    background: linear-gradient(135deg, #fde6cf 0%, #fcd3a8 45%, #f7b273 100%);
  }
  .hero-photo {
    position: absolute; right: 0; top: 0; width: 330px; height: 267px;
    background: linear-gradient(90deg, rgba(252,222,190,0) 0%, #efe1d3 30%, #e6d6c8 70%, #d9c8b8 100%);
  }
  .hero-title {
    position: absolute; left: 25px; top: 48px;
    font-size: 37px; font-weight: 600; line-height: 39px; color: var(--ink);
    letter-spacing: -0.3px;
  }
  .hero-subtitle {
    position: absolute; left: 25px; top: 131px;
    font-size: 25px; font-weight: 300; color: var(--ink);
  }
  .session-band {
    position: absolute; left: 0; top: 189px; width: 400px; height: 39px;
    background: linear-gradient(90deg, #fff 0%, #fff 70%, rgba(255,255,255,0) 100%);
  }
  .session-band span {
    position: absolute; left: 24px; top: 4px;
    font-size: 24px; font-weight: 600; color: var(--ink);
  }
  .services {
    position: absolute; left: 17px; top: 284px; width: 645px; height: 207px;
    background: linear-gradient(180deg, var(--orange-light) 0%, var(--orange) 45%, var(--orange-deep) 100%);
    color: #fff;
  }
  .services-heading {
    position: absolute; left: 0; right: 0; top: 22px; text-align: center;
    font-size: 14.5px; font-weight: 600; letter-spacing: 0.2px;
  }
  .service {
    position: absolute; top: 64px; width: 126px; margin-left: -63px; text-align: center;
  }
  .service-icon {
    width: 74px; height: 74px; margin: 0 auto;
    border: 1.5px solid #fff; border-radius: 7px; background: var(--orange);
    display: flex; align-items: center; justify-content: center;
  }
  .service-icon i { display: block; width: 46px; height: 46px; border-radius: 4px; background: #fde0c2; }
  .service-label { margin-top: 17px; font-size: 12px; font-weight: 600; line-height: 15px; }
  .event {
    position: absolute; left: 17px; top: 491px; width: 645px; height: 121px;
    background: var(--slate); color: #fff; text-align: center;
  }
  .event-when { margin-top: 17px; font-size: 20.5px; font-weight: 600; }
  .event-when .date { color: var(--gold); }
  .event-where { font-size: 15.5px; font-weight: 300; line-height: 19.5px; }
  .event-note { margin: 9px auto 0; width: 420px; font-size: 8px; line-height: 11px; font-weight: 300; }
  .about { position: absolute; top: 632px; font-size: 10.6px; line-height: 13.7px; text-align: justify; }
  .about p + p { margin-top: 10px; }
  .about-left { left: 33px; width: 262px; }
  .about-right { left: 372px; width: 262px; }
  .about-right p + p { margin-top: 16px; }
  .about b { font-weight: 600; color: var(--ink); }
  .divider { position: absolute; left: 340px; top: 624px; width: 1px; height: 146px; background: var(--rule); }
  .partners {
    position: absolute; left: 76px; top: 772px; width: 527px; height: 72px;
    border: 1px solid #9a9a9e; border-radius: 8px;
    display: flex; align-items: center; justify-content: space-around; padding: 0 20px;
  }
  .partner { font-weight: 600; font-size: 18px; color: var(--slate); display: flex; align-items: center; gap: 7px; }
  .partner-mark { width: 22px; height: 22px; border-radius: 50%; background: var(--orange); }
  .partner-small { font-size: 10px; line-height: 11px; font-weight: 500; }
  .more-info { position: absolute; left: 39px; top: 880px; font-size: 11.5px; line-height: 15px; color: var(--text); }
  .more-info .url { display: block; margin-top: 3px; font-weight: 600; font-size: 12.5px; color: var(--ink); }
  .brand {
    position: absolute; right: 40px; top: 902px; display: flex; align-items: center; gap: 8px;
  }
  .brand-mark { width: 14px; height: 14px; background: var(--orange); }
  .brand-name { font-size: 18px; font-weight: 600; line-height: 20px; color: var(--slate); }
  .base-bar { position: absolute; left: 0; bottom: 0; width: 680px; height: 11px; background: var(--orange-deep); }
</style>
</head>
<body>
<main class="flyer">
  <section class="hero">
    <div class="hero-photo" role="img" aria-label="Photograph of a young girl playing with a yellow toy block"></div>
    <h1 class="hero-title">The Willow<br>Gate Community</h1>
    <p class="hero-subtitle">Service Announcement</p>
    <div class="session-band"><span>Information Session</span></div>
  </section>

  <section class="services">
    <h2 class="services-heading">THE SERVICES OFFERED BY THE WILLOW GATE ARE:</h2>
    <div class="service" style="left:104px">
      <div class="service-icon"><i role="img" aria-label="Icon of a family group"></i></div>
      <p class="service-label">Women, children and young people’s family violence services</p>
    </div>
    <div class="service" style="left:256px">
      <div class="service-icon"><i role="img" aria-label="Icon of a parent with children"></i></div>
      <p class="service-label">Child and family services</p>
    </div>
    <div class="service" style="left:409px">
      <div class="service-icon"><i role="img" aria-label="Icon of an Aboriginal elder"></i></div>
      <p class="service-label">Aboriginal services</p>
    </div>
    <div class="service" style="left:562px">
      <div class="service-icon"><i role="img" aria-label="Icon of a group of men"></i></div>
      <p class="service-label">Men’s family violence services</p>
    </div>
  </section>

  <section class="event">
    <p class="event-when">Wednesday, <span class="date">October 09, 2019</span> | 3pm - 7pm</p>
    <p class="event-where">the Tenby &amp; District Aboriginal Co-Operative office<br>12 Harbour Street, Tenby.</p>
    <p class="event-note">At the information session you’ll have the opportunity to hear from all of the agency partners who are part of The Willow Gate, as well as hear from some current practitioners and ask questions.</p>
  </section>

  <div class="about about-left">
    <p>The Willow Gate is a free service for adults, children and young people who are experiencing, or have experienced, family violence and for families who need extra support with the care of children.</p>
    <p>The aim is to strengthen support for children and families and involves a partnership between Pellman Lane, DRUK and the Tenby &amp; District Aboriginal Co-Operative.</p>
  </div>
  <div class="divider"></div>
  <div class="about about-right">
    <p>Last year, The Willow Gate opened in <b>Barwon, Bayside Peninsula, Inner Gippsland, Mallee and North Eastern Melbourne.</b></p>
    <p>Early next year The Willow Gate will be opening in the Central Highlands area, so we’re currently looking for specialist practitioners who want to be part of this meaningful work.</p>
  </div>

  <section class="partners">
    <div class="partner"><span class="partner-mark"></span><span class="partner-small">Tenby and District<br>Aboriginal Co-operative</span></div>
    <div class="partner">Pellman Lane</div>
    <div class="partner">DRUK</div>
  </section>

  <p class="more-info">For more information, head to<span class="url">www.familysupport.example.org</span>and check out the latest news section</p>

  <div class="brand">
    <span class="brand-mark"></span>
    <span class="brand-name">The Willow Gate</span>
  </div>

  <div class="base-bar"></div>
</main>
</body>
</html>
```